Bramwell IT Services Business Card

Bramwell IT Services are a Perth based IT Services company. We would like to incorporate our company logo (attached) and stick with the blue that is in that design. I would like a clean look design that isn't too busy, yet creates a lasting image that is instantly recognisable in the recipients mind.

Target Market(s)

The target audience is small/medium business owners.

Industry/Entity Type

Business

Font styles to use
Serif
Sans Serif

Colors

Designer to choose colors to be used in the design.

Requirements
Must have
• The design should include:
Business name: Bramwell IT Services
Directors Name: Marcus Tenley
Phone Number: 0483 562 904
Email: support@bramwellit.com.au
Website: www.bramwellit.com.au

```html
<!DOCTYPE html>
<html lang="en">
<head>
<meta charset="utf-8">
<title>Bramwell IT Services – Business Card</title>
<link href="https://fonts.googleapis.com/css2?family=Exo+2:ital,wght@0,400;0,500;1,500&display=swap" rel="stylesheet">
<style>
  :root {
    --bg: #e6e8eb;
    --card-white: #f4f5f6;
    --card-grey: #d9dcdf;
    --blue-deep: #0c6fd1;
    --blue-mid: #1d95e6;
    --blue-light: #38d3fa;
    --text-light: #ffffff;
    --text-blue: #1379d8;
  }
  * { margin: 0; padding: 0; box-sizing: border-box; }
  html, body { width: 1200px; height: 903px; overflow: hidden; }
  body {
    background: var(--bg);
    font-family: "Exo 2", sans-serif;
    position: relative;
  }
  .card {
    position: absolute;
    width: 640px;
    height: 360px;
    overflow: hidden;
    background: linear-gradient(135deg, var(--card-white), var(--card-grey));
    box-shadow: 0 6px 18px rgba(0,0,0,0.18);
  }
  .card-back { left: 70px; top: 50px; }
  .card-front { left: 490px; top: 490px; }
  .card-shapes { position: absolute; inset: 0; width: 100%; height: 100%; }

  .brand {
    position: absolute;
    display: flex;
    align-items: center;
    gap: 10px;
    color: var(--blue-deep);
    font-weight: 500;
  }
  .brand-square {
    width: 18px; height: 18px;
    background: var(--blue-mid);
  }
  .card-back .brand { left: 0; right: 0; top: 70px; justify-content: center; font-size: 26px; }
  .card-front .brand { left: 34px; top: 120px; font-size: 22px; flex-direction: column; align-items: flex-start; gap: 8px; line-height: 1.15; }
  .card-front .brand .brand-square { width: 26px; height: 26px; }

  .back-web {
    position: absolute; right: 40px; top: 200px;
    color: var(--text-light); font-size: 18px; letter-spacing: 3px;
  }
  .follow {
    position: absolute; right: 40px; top: 250px;
    display: flex; align-items: center; gap: 12px;
    color: var(--text-light); font-size: 18px; letter-spacing: 2px;
  }
  .social-dot { width: 22px; height: 22px; border-radius: 50%; background: var(--text-light); }

  .person { position: absolute; left: 330px; top: 22px; color: var(--text-light); font-style: italic; }
  .person-name { font-size: 24px; font-weight: 500; letter-spacing: 1px; text-transform: uppercase; }
  .person-role { font-size: 15px; padding-left: 16px; }

  .address {
    position: absolute; right: 24px; top: 150px;
    color: var(--text-light); font-size: 15px; text-align: right; line-height: 1.45; letter-spacing: 0.5px;
  }
  .contacts {
    position: absolute; right: 24px; top: 220px;
    list-style: none; color: var(--text-light); font-size: 13px; letter-spacing: 1px;
  }
  .contacts li { display: flex; justify-content: flex-end; align-items: center; gap: 8px; height: 24px; }
  .contacts svg { width: 14px; height: 14px; fill: none; stroke: var(--text-light); stroke-width: 1.8; }
</style>
</head>
<body>

<section class="card card-back" aria-label="Card back">
  <svg class="card-shapes" viewBox="0 0 640 360" preserveAspectRatio="none">
    <defs>
      <linearGradient id="backBlue" x1="0" y1="1" x2="1" y2="0">
        <stop offset="0" stop-color="#0c6fd1"/>
        <stop offset="0.6" stop-color="#2bb2f0"/>
        <stop offset="1" stop-color="#1d95e6"/>
      </linearGradient>
    </defs>
    <polygon points="0,290 640,150 640,360 0,360" fill="url(#backBlue)"/>
  </svg>
  <div class="brand"><span class="brand-square"></span>Bramwell IT Services</div>
  <p class="back-web">www.bramwellit.com.au</p>
  <div class="follow">follow us on here:
    <span class="social-dot"></span><span class="social-dot"></span><span class="social-dot"></span><span class="social-dot"></span>
  </div>
</section>

<section class="card card-front" aria-label="Card front">
  <svg class="card-shapes" viewBox="0 0 640 360" preserveAspectRatio="none">
    <defs>
      <radialGradient id="frontBlue" cx="0.6" cy="0.55" r="0.6">
        <stop offset="0" stop-color="#38d3fa"/>
        <stop offset="1" stop-color="#0f7ad8"/>
      </radialGradient>
      <linearGradient id="panelBlue" x1="0" y1="0" x2="1" y2="1">
        <stop offset="0" stop-color="#1d95e6"/>
        <stop offset="1" stop-color="#2bbcf3"/>
      </linearGradient>
    </defs>
    <polygon points="0,330 560,60 640,150 640,360 0,360" fill="url(#frontBlue)"/>
    <polygon points="300,0 640,0 640,10 330,170" fill="url(#panelBlue)"/>
  </svg>
  <div class="brand"><span class="brand-square"></span>Bramwell<br>IT Services</div>
  <div class="person">
    <p class="person-name">Marcus Tenley</p>
    <p class="person-role">Managing Director</p>
  </div>
  <p class="address">Level 18, 42 Harlow Street<br>Perth WA</p>
  <ul class="contacts">
    <li>08 9412 7730
      <svg viewBox="0 0 16 16"><path d="M4 2l2 3-1.5 1.5c1 2 2.5 3.5 4.5 4.5L10.5 9.5l3 2-1 2.5C7 14 2 9 2 3.5z"/></svg></li>
    <li>0483 562 904
      <svg viewBox="0 0 16 16"><rect x="4.5" y="1.5" width="7" height="13" rx="1.2"/><line x1="7" y1="12.5" x2="9" y2="12.5"/></svg></li>
    <li>08 9412 7731
      <svg viewBox="0 0 16 16"><rect x="2" y="6" width="12" height="8"/><rect x="5" y="2" width="6" height="4"/></svg></li>
    <li>support@bramwellit.com.au
      <svg viewBox="0 0 16 16"><rect x="1.5" y="3.5" width="13" height="9"/><path d="M1.5 3.5l6.5 5 6.5-5"/></svg></li>
    <li>www.bramwellit.com.au
      <svg viewBox="0 0 16 16"><circle cx="8" cy="8" r="6.5"/><ellipse cx="8" cy="8" rx="2.8" ry="6.5"/><line x1="1.5" y1="8" x2="14.5" y2="8"/></svg></li>
  </ul>
</section>

</body>
</html>
```